Brightfen Business Card Redesign & Logo Update

We need to update our business cards to something more modern and fresh. Brightfen can provide the current color schemes and old design examples, but welcome creativity in helping us with this redesign. PLEASE NOTE that we no longer utilize the "tree" and/or "leaf" imagery in our branding. If able would apprecaite an update on the quality of our "words only" logo in Ai. / PNG formats too.

Target Market(s)

Investors, landowners, corporate partners, contractors

Industry/Entity Type

Environmental Restoration & Conservation

Contact Information for Business Card

Logo, persons name, title, mailing address, phone and email, website url

Font styles to use
Other font styles liked:
• Merriweather

Requirements
Nice to have
• Logo, persons name, title, mailing address, phone and email, website url, but open to ideams
Should not have
• No all back backgrounds

```html
<!DOCTYPE html>
<html lang="en">
<head>
<meta charset="utf-8">
<title>Brightfen Business Card</title>
<link rel="stylesheet" href="https://fonts.googleapis.com/css2?family=Bebas+Neue&family=Arimo:wght@400&display=swap">
<style>
  :root {
    --orange: #dc7000;
    --green: #0f7233;
    --white: #ffffff;
    --ink: #1a1a1a;
    --grey: #6d6d6d;
    --stage: #d9d9d9;
  }
  html, body {
    margin: 0;
    padding: 0;
    width: 1200px;
    height: 793px;
    overflow: hidden;
    background: var(--stage);
  }
  .canvas {
    position: relative;
    width: 1200px;
    height: 793px;
  }
  .card {
    position: absolute;
    top: 245px;
    width: 530px;
    height: 303px;
    border-radius: 22px;
    overflow: hidden;
    box-shadow: 0 3px 0 var(--green), 0 10px 24px rgba(0,0,0,0.18);
  }
  .card--front { left: 50px; background: var(--white); }
  .card--back { left: 620px; background: var(--orange); }
  .card__wave {
    position: absolute;
    inset: 0;
  }
  .wordmark {
    position: absolute;
    font-family: "Bebas Neue", sans-serif;
    line-height: 0.85;
    letter-spacing: 1px;
    margin: 0;
  }
  .tagline {
    font-family: "Bebas Neue", sans-serif;
    display: block;
    letter-spacing: 0.5px;
  }
  .card--front .wordmark {
    left: 36px;
    top: 74px;
    font-size: 56px;
    color: var(--orange);
  }
  .card--front .tagline {
    font-size: 15.5px;
    color: var(--ink);
    margin-top: 4px;
  }
  .person {
    position: absolute;
    left: 36px;
    top: 160px;
  }
  .person__name {
    font-family: "Bebas Neue", sans-serif;
    font-size: 30px;
    line-height: 1;
    margin: 0;
    letter-spacing: 0.5px;
  }
  .person__first { color: var(--orange); }
  .person__last { color: var(--green); }
  .person__title {
    font-family: "Arimo", sans-serif;
    font-size: 13px;
    color: var(--grey);
    margin: 3px 0 0;
  }
  .contact {
    position: absolute;
    right: 26px;
    top: 100px;
    margin: 0;
    padding: 0;
    list-style: none;
    font-family: "Arimo", sans-serif;
    font-size: 12.5px;
    line-height: 1.45;
    color: var(--white);
    text-align: right;
  }
  .contact li {
    display: flex;
    justify-content: flex-end;
    align-items: center;
    gap: 6px;
  }
  .contact svg { width: 11px; height: 11px; flex: none; }
  .contact .spacer { width: 11px; flex: none; }
  .card--back .wordmark {
    left: 0;
    right: 0;
    top: 88px;
    text-align: center;
    font-size: 124px;
    color: var(--white);
  }
  .card--back .tagline {
    font-size: 31px;
    margin-top: 4px;
    letter-spacing: 0.8px;
  }
</style>
</head>
<body>
<main class="canvas">

  <section class="card card--front" aria-label="Business card front">
    <svg class="card__wave" viewBox="0 0 530 303" preserveAspectRatio="none" aria-hidden="true">
      <path d="M0,262 C170,262 250,230 300,150 C345,60 365,12 450,-2 L530,-2 L530,303 L0,303 Z" fill="var(--green)"/>
      <path d="M0,278 C180,278 262,244 312,164 C355,76 378,26 462,12 L530,12 L530,303 L0,303 Z" fill="var(--orange)" stroke="var(--white)" stroke-width="2"/>
    </svg>

    <h1 class="wordmark">Brightfen<span class="tagline">Environmental Credit Company</span></h1>

    <div class="person">
      <p class="person__name"><span class="person__first">Daniel</span> <span class="person__last">Morrow</span></p>
      <p class="person__title">Managing Director</p>
    </div>

    <ul class="contact">
      <li>412 Larkspur Way<span class="spacer"></span></li>
      <li>Juneau, Alaska 99801<span class="spacer"></span></li>
      <li>555-210-4837
        <svg viewBox="0 0 12 12" aria-hidden="true"><path d="M2.5 1 L4.5 1 L5.3 3.6 L4 4.6 C4.7 6 6 7.3 7.4 8 L8.4 6.7 L11 7.5 L11 9.5 C11 10.4 10.3 11 9.5 11 C5 11 1 7 1 2.5 C1 1.7 1.6 1 2.5 1 Z" fill="var(--white)"/></svg>
      </li>
      <li>555-318-6620
        <svg viewBox="0 0 12 12" aria-hidden="true"><rect x="3" y="0.8" width="6" height="10.4" rx="1" fill="none" stroke="var(--white)" stroke-width="1.2"/><circle cx="6" cy="9.4" r="0.7" fill="var(--white)"/></svg>
      </li>
      <li>info@brightfen.com
        <svg viewBox="0 0 12 12" aria-hidden="true"><rect x="0.8" y="2.5" width="10.4" height="7.4" fill="var(--white)"/><path d="M0.8 2.5 L6 6.6 L11.2 2.5" fill="none" stroke="var(--orange)" stroke-width="1"/></svg>
      </li>
      <li>www.brightfen.com<span class="spacer"></span></li>
    </ul>
  </section>

  <section class="card card--back" aria-label="Business card back">
    <h2 class="wordmark">Brightfen<span class="tagline">Environmental Credit Company</span></h2>
  </section>

</main>
</body>
</html>
```